Marlow Estate Fixers (Handyman / Home Improvement Company)

Looking for a double sided professional looking business card with Logo attached to be highlighted on one side and throwing in an image of a handyman as an option would be nice to see as well. We are a company focused on providing quality Handyman and Home improvement services in a timely manner that is done right the first time with integrity

Industry/Entity Type

Handyman / Home Improvement

Contact Information for Business Card

(LOGO, Name, Mobile and office phone numbers, email) on front side of card, (the words "The SOLUTION to all of your Handyman and Home Improvement needs" followed by "Family Owned and Operated" at the very bottom) on the back.

Colors
EB3D1F
EC4F4E
F09395
F8D3D4
FCEDEE

Requirements
Must have
• Red, Gray, Black Color scheme
Should not have
• No Yellow or Blue colors

```html
<!DOCTYPE html>
<html lang="en">
<head>
<meta charset="utf-8">
<title>Marlow Estate Fixers – Business Card</title>
<link rel="stylesheet" href="https://fonts.googleapis.com/css2?family=Montserrat:wght@400;800;900&family=Poppins:wght@400&family=EB+Garamond:wght@400&display=swap">
<style>
  :root {
    --stage: #5e5e5e;
    --brand-red: #e82c2f;
    --brand-red-deep: #d92528;
    --ink: #151515;
    --white: #ffffff;
    --silver-light: #f6f6f6;
    --silver-mid: #d9d9d9;
    --silver-dark: #bdbdbd;
  }
  * { box-sizing: border-box; margin: 0; padding: 0; }
  html, body { width: 1200px; height: 900px; overflow: hidden; }
  body {
    background: var(--stage);
    position: relative;
    font-family: "Montserrat", sans-serif;
  }
  .card {
    position: absolute;
    width: 640px;
    height: 366px;
    border-radius: 28px;
    overflow: hidden;
    box-shadow: 0 18px 34px rgba(0,0,0,0.35);
  }

  /* Back side */
  .card--back {
    left: 80px; top: 70px;
    background: linear-gradient(135deg, var(--brand-red) 0%, var(--brand-red-deep) 100%);
    color: var(--white);
    display: flex; flex-direction: column; align-items: center; justify-content: center;
    text-align: center;
  }
  .brand-name {
    display: flex; align-items: center; gap: 14px;
    font-weight: 800; text-transform: uppercase; line-height: 1;
  }
  .brand-name__dot { border-radius: 50%; flex: none; }
  .card--back .brand-name { font-size: 40px; color: var(--white); margin-bottom: 38px; }
  .card--back .brand-name__dot { width: 30px; height: 30px; background: var(--white); }
  .tagline {
    font-weight: 800; font-size: 15px; letter-spacing: 0.3px; line-height: 1.35;
    text-transform: uppercase;
  }
  .heritage {
    font-family: "EB Garamond", serif;
    font-size: 17px; margin-top: 16px; letter-spacing: 0.5px;
  }

  /* Front side */
  .card--front {
    left: 480px; top: 464px;
    background: linear-gradient(120deg, var(--silver-dark) 0%, var(--silver-light) 35%, var(--silver-mid) 60%, var(--silver-light) 82%, var(--silver-dark) 100%);
    color: var(--ink);
  }
  .front__watermark {
    position: absolute; left: 110px; top: 150px;
    width: 300px; height: 300px; border-radius: 50%;
    background: radial-gradient(circle, rgba(255,255,255,0.55), rgba(255,255,255,0) 70%);
  }
  .front__brand {
    position: absolute; right: 34px; top: 44px;
  }
  .card--front .brand-name { font-size: 28px; color: var(--ink); gap: 10px; }
  .card--front .brand-name__dot { width: 24px; height: 24px; background: var(--brand-red); }
  .holder {
    position: absolute; left: 0; top: 168px;
    display: flex; align-items: center; gap: 20px;
  }
  .holder__marker { width: 30px; height: 34px; background: var(--brand-red); }
  .holder__name {
    font-weight: 900; font-size: 30px; color: var(--brand-red);
    text-transform: uppercase; letter-spacing: 0.5px;
  }
  .contacts {
    position: absolute; left: 56px; bottom: 40px;
    list-style: none; font-family: "Poppins", sans-serif;
    font-size: 21px; line-height: 1.45; color: var(--ink);
  }
  .contacts li { display: flex; align-items: center; gap: 14px; }
  .contacts svg { width: 20px; height: 20px; flex: none; }
</style>
</head>
<body>

  <section class="card card--back" aria-label="Card back">
    <div class="brand-name"><span class="brand-name__dot"></span>Marlow Estate Fixers</div>
    <p class="tagline">Your solution to all of your<br>handyman and home improvement needs</p>
    <p class="heritage">Family Owned and Operated</p>
  </section>

  <section class="card card--front" aria-label="Card front">
    <div class="front__watermark"></div>
    <div class="front__brand">
      <div class="brand-name"><span class="brand-name__dot"></span>Marlow Estate Fixers</div>
    </div>
    <div class="holder">
      <span class="holder__marker"></span>
      <h1 class="holder__name">Daniel Reeve</h1>
    </div>
    <ul class="contacts">
      <li>
        <svg viewBox="0 0 20 20" aria-hidden="true"><rect x="5" y="2" width="10" height="16" rx="2" fill="none" stroke="#e82c2f" stroke-width="2"/><circle cx="10" cy="15" r="1" fill="#e82c2f"/></svg>
        044-555 010 234
      </li>
      <li>
        <svg viewBox="0 0 20 20" aria-hidden="true"><path d="M5 3 L8 3 L9 7 L7 8.5 C8 11 9.5 12.5 12 13.5 L13.5 11.5 L17 12.5 L17 16 C11 17 3 9 5 3 Z" fill="#e82c2f"/></svg>
        044-555 010 876
      </li>
      <li>
        <svg viewBox="0 0 20 20" aria-hidden="true"><rect x="2" y="5" width="16" height="11" fill="#e82c2f"/><path d="M2 5 L10 11 L18 5" fill="none" stroke="#fff" stroke-width="1.5"/></svg>
        hello@marlowfixers.com
      </li>
    </ul>
  </section>

</body>
</html>
```